Storm Restoration Contractor needs a professional letterhead design

Looking for a professional letterhead design. Not looking for your cheapo MS Word standard ones that are readily available. Dont want it to be cookie cutter look like ones readily available online. We just recently changed our logo and want to freshen up all our documents. Our company handles restoring a property back to a pre-loss condition after a storm damages it. For example, wind, hail, flood, fire losses.

Target Market(s)

Property Owners, Homeowners, Property Owners, Commercial Property Owners, Property Management Companies

Industry/Entity Type

Construction Company

Requirements
Must have
• Professional, Use 1 of 2 logo options
• Storm Restoration, Roofing, Siding, Windows

```html
<!DOCTYPE html>
<html lang="en">
<head>
<meta charset="utf-8">
<title>Renewed Facades Letterhead</title>
<link rel="stylesheet" href="https://fonts.googleapis.com/css2?family=Questrial&display=swap">
<style>
  :root {
    --backdrop: #c9c9c9;
    --paper: #f1f1f1;
    --brand-blue: #1f63b0;
    --ink: #444444;
    --rule: #b5b5b5;
    --accent-pale: #adc6dc;
  }
  * { margin: 0; padding: 0; box-sizing: border-box; }
  html, body {
    width: 1200px;
    height: 1041px;
    overflow: hidden;
    background: var(--backdrop);
    font-family: "Questrial", "Century Gothic", sans-serif;
  }
  .letterhead {
    position: absolute;
    left: 212px;
    top: 20px;
    width: 775px;
    height: 1001px;
    background: var(--paper);
    overflow: hidden;
  }
  .corner-ring {
    position: absolute;
    left: 0;
    top: 0;
  }
  .brand {
    position: absolute;
    left: 58px;
    top: 66px;
    display: flex;
    align-items: center;
    gap: 14px;
  }
  .brand-dot {
    width: 56px;
    height: 56px;
    border-radius: 50%;
    background: var(--brand-blue);
  }
  .brand-name {
    color: var(--brand-blue);
    font-size: 22px;
    line-height: 24px;
    letter-spacing: 1.5px;
    text-transform: uppercase;
  }
  .footer-rule {
    position: absolute;
    left: 59px;
    top: 927px;
    width: 657px;
    height: 1px;
    background: var(--rule);
  }
  .footer {
    position: absolute;
    left: 59px;
    top: 940px;
    width: 657px;
    display: flex;
    justify-content: space-between;
    font-size: 10px;
    line-height: 14px;
    color: var(--ink);
  }
  .label, .web-name {
    color: var(--brand-blue);
    font-weight: bold;
  }
</style>
</head>
<body>
  <main class="letterhead">
    <svg class="corner-ring" width="775" height="360" viewBox="0 0 775 360" aria-hidden="true">
      <circle cx="688" cy="142" r="160" fill="none" stroke="var(--accent-pale)" stroke-width="26"/>
    </svg>

    <header class="brand">
      <div class="brand-dot"></div>
      <div class="brand-name">Renewed<br>Facades</div>
    </header>

    <div class="footer-rule"></div>
    <footer class="footer">
      <div class="contact">
        <p>4120 N Canyon View Road STE 210, Mesa, AZ 85203</p>
        <p><span class="label">T:</span> 555-014-2200 · <span class="label">F:</span> 555-014-2200 · <span class="label">E:</span> hello@renewedfacades.com</p>
      </div>
      <p class="web">www.<span class="web-name">renewedfacades</span>.com</p>
    </footer>
  </main>
</body>
</html>
```